Automotive spring company needs banner for website

Banner dimensions: 3840 x 880 pixels
Banner need to be consistent with our branding (logo, stationary, colors, fonts, message).
People images should show happiness and it is preferable those people are in or around a car unless it ties into one of the 3 quotes in the must haves below.
Use color blue #4885ed
and gold color #f7d105
Minimal, strong, clean, & tech

35-55 male and female

Auto Repair

• Clickable element for "Shop" or "Make an Appointment"
• "25 Years of Customer Satisfaction" or
• "Get it Done Right by Specialist" or
• "Peace of Mind National Warranty"
• Use our font, Eurostile and/or complimentary font paring

```html
<!DOCTYPE html>
<html lang="en">
<head>
<meta charset="utf-8">
<title>25 Years of Customer Satisfaction – Web Banners</title>
<link rel="stylesheet" href="https://fonts.googleapis.com/css2?family=Michroma&family=Montserrat:ital,wght@0,700;1,400&family=Questrial&display=swap">
<style>
  :root {
    --stage: #1b0057;
    --brand-blue: #4885ed;
    --brand-gold: #f7d105;
    --ink: #1a1a1a;
    --white: #ffffff;
  }
  html, body {
    margin: 0;
    padding: 0;
    width: 1200px;
    height: 1200px;
    overflow: hidden;
    background: var(--stage);
  }
  .stage {
    position: relative;
    width: 1200px;
    height: 1200px;
  }
  .banner {
    position: absolute;
    left: 0;
    width: 1200px;
    height: 275px;
    display: block;
  }
  .banner--sunshine { top: 314px; }
  .banner--city { top: 617px; }
  .brand-blue { fill: var(--brand-blue); }
  .brand-gold { fill: var(--brand-gold); }
  .headline {
    font-family: "Michroma", sans-serif;
    font-size: 58px;
    fill: var(--brand-gold);
    stroke: var(--brand-gold);
    stroke-width: 0.8px;
  }
  .subline {
    font-family: "Montserrat", sans-serif;
    font-style: italic;
    font-weight: 400;
    font-size: 26px;
    fill: var(--white);
  }
  .tagline {
    font-family: "Questrial", sans-serif;
    font-size: 17px;
    fill: var(--white);
  }
  .rule {
    stroke: var(--brand-gold);
    stroke-width: 2;
  }
  .cta-label {
    font-family: "Montserrat", sans-serif;
    font-weight: 700;
    font-size: 10.5px;
    letter-spacing: 1.6px;
    fill: var(--ink);
  }
  .cta-shadow { fill: #3a6cc4; }
  .cta { cursor: pointer; }
</style>
</head>
<body>
<main class="stage">

  <svg class="banner banner--sunshine" viewBox="0 0 1200 275" xmlns="http://www.w3.org/2000/svg">
    <defs>
      <radialGradient id="sunshine-photo" cx="0.52" cy="0.62" r="0.75" fx="0.5" fy="0.55">
        <stop offset="0" stop-color="#f3c623"/>
        <stop offset="0.28" stop-color="#f0d36a"/>
        <stop offset="0.55" stop-color="#efe0c4"/>
        <stop offset="0.8" stop-color="#c8bba4"/>
        <stop offset="1" stop-color="#6f6a64"/>
      </radialGradient>
    </defs>
    <rect class="brand-blue" x="0" y="0" width="1200" height="275"/>
    <rect class="brand-gold" x="78" y="0" width="17" height="275"/>
    <polygon points="95,0 800,0 696,275 95,275" fill="url(#sunshine-photo)" role="img" aria-label="Photo: happy woman in a yellow shirt standing in an open convertible, arms spread wide in warm sunlight"/>
    <polygon class="brand-gold" points="798,0 815,0 712,275 694,275"/>
    <text class="headline" x="827" y="110" textLength="331" lengthAdjust="spacingAndGlyphs">25YEARS</text>
    <text class="subline" x="828" y="138" textLength="330" lengthAdjust="spacingAndGlyphs">of Customer Satisfaction</text>
    <line class="rule" x1="830" y1="151" x2="1156" y2="151"/>
    <text class="tagline" x="835" y="173" textLength="322" lengthAdjust="spacingAndGlyphs">GET IT DONE RIGHT BY SPECIALIST</text>
    <line class="rule" x1="830" y1="181" x2="1156" y2="181"/>
    <g class="cta" role="link" aria-label="Make an appointment">
      <rect class="cta-shadow" x="893" y="199" width="198" height="28" rx="6"/>
      <rect class="brand-gold" x="892" y="197" width="198" height="28" rx="6"/>
      <text class="cta-label" x="991" y="215" text-anchor="middle">MAKE AN APPOINTMENT</text>
    </g>
  </svg>

  <svg class="banner banner--city" viewBox="0 0 1200 275" xmlns="http://www.w3.org/2000/svg">
    <defs>
      <radialGradient id="city-photo" cx="0.42" cy="0.7" r="0.7" fx="0.4" fy="0.65">
        <stop offset="0" stop-color="#f2cf32"/>
        <stop offset="0.45" stop-color="#e7bd22"/>
        <stop offset="0.7" stop-color="#a78a2a"/>
        <stop offset="0.88" stop-color="#4a4535"/>
        <stop offset="1" stop-color="#2a2a24"/>
      </radialGradient>
    </defs>
    <rect class="brand-blue" x="0" y="0" width="1200" height="275"/>
    <rect class="brand-gold" x="78" y="0" width="17" height="275"/>
    <polygon points="95,0 800,0 696,275 95,275" fill="url(#city-photo)" role="img" aria-label="Photo: smiling woman in an off-shoulder top walking beside a bright yellow compact car"/>
    <polygon class="brand-gold" points="798,0 815,0 712,275 694,275"/>
    <text class="headline" x="832" y="110" textLength="331" lengthAdjust="spacingAndGlyphs">25YEARS</text>
    <text class="subline" x="833" y="138" textLength="330" lengthAdjust="spacingAndGlyphs">of Customer Satisfaction</text>
    <line class="rule" x1="835" y1="151" x2="1161" y2="151"/>
    <text class="tagline" x="840" y="173" textLength="322" lengthAdjust="spacingAndGlyphs">GET IT DONE RIGHT BY SPECIALIST</text>
    <line class="rule" x1="835" y1="181" x2="1161" y2="181"/>
    <g class="cta" role="link" aria-label="Make an appointment">
      <rect class="cta-shadow" x="898" y="199" width="198" height="28" rx="6"/>
      <rect class="brand-gold" x="897" y="197" width="198" height="28" rx="6"/>
      <text class="cta-label" x="996" y="215" text-anchor="middle">MAKE AN APPOINTMENT</text>
    </g>
  </svg>

</main>
</body>
</html>
```